Meridale Staffing Website

My business has been word of mouth over the last 3 years and has grown. Now I need a website for additional marketing as we have new clients asking for a website.

You have already completed my Logo during an earlier project. I have attached the logo.

We do Staff Augmentation and Operation Support.

What is that?
Staff augmentation is an outsourcing strategy that allows companies to fill specific, temporary roles to achieve business objectives. This staffing method complements existing teams with specific talent, enhancing business capabilities or filling gaps left by members on extended leave.

We work alongside the internal recruiting team to assist clients to meet and exceed financial goals.

```html
<!DOCTYPE html>
<html lang="en">
<head>
<meta charset="utf-8">
<title>Meridale Staffing</title>
<link href="https://fonts.googleapis.com/css2?family=Roboto:ital,wght@0,400;0,500;0,700;0,900;1,400&display=swap" rel="stylesheet">
<style>
:root{
  --navy:#0f3d66;
  --navy-deep:#0b3458;
  --orange:#f7941d;
  --gray:#6d6e71;
  --gray-light:#eef0f3;
  --dark:#2b2b2d;
  --text:#555a60;
  --white:#fff;
}
*{box-sizing:border-box;margin:0;padding:0}
html,body{width:1200px;height:4431px;overflow:hidden}
body{font-family:'Roboto',sans-serif;color:var(--text);background:var(--white);position:relative}
.abs{position:absolute}
/* header */
.site-header{position:absolute;left:0;top:0;width:1200px;height:107px;background:var(--white);z-index:5}
.brand{position:absolute;left:110px;top:26px;display:flex;align-items:center;gap:10px}
.brand-dot{width:50px;height:50px;border-radius:50%;background:var(--navy)}
.brand-name{font-weight:700;color:var(--navy);font-size:26px;line-height:1}
.brand-name small{display:block;font-size:15px;font-weight:400;color:var(--navy);letter-spacing:1px;margin-top:3px}
.call{position:absolute;left:874px;top:18px;display:flex;align-items:center;gap:14px}
.call-icon{width:38px;height:38px;border-radius:50%;background:var(--navy);display:flex;align-items:center;justify-content:center}
.call-text{font-size:12px;font-weight:700;color:var(--dark)}
.call-text b{display:block;font-size:20px;color:var(--navy)}
.main-nav{position:absolute;left:475px;top:76px;display:flex;gap:33px;font-size:13px;font-weight:700;color:var(--dark)}
.main-nav .active{color:var(--navy);position:relative}
.main-nav .active::before{content:"";position:absolute;left:50%;top:-11px;width:6px;height:6px;margin-left:-3px;border-radius:50%;background:var(--gray)}
/* hero */
.hero{position:absolute;left:0;top:107px;width:1200px;height:830px}
.hero-photo{position:absolute;inset:0;background:linear-gradient(110deg,#b9c0c7 0%,#dfe3e6 40%,#8e969c 70%,#3a3f46 100%)}
.hero h1{position:absolute;left:110px;top:150px;font-size:59px;line-height:76px;font-weight:900;color:var(--white);letter-spacing:.5px}
.btn{position:absolute;display:flex;align-items:center;justify-content:space-between;height:46px;border-radius:23px;padding:0 8px 0 24px;font-size:13px;font-weight:700;color:var(--white);text-transform:uppercase}
.btn i{width:34px;height:34px;border-radius:50%;background:var(--white);display:block;margin-left:16px}
.btn-navy{background:var(--navy)}
.btn-orange{background:var(--orange)}
.slide-arrow{position:absolute;width:30px;height:40px}
/* about */
.about-photo-ring{position:absolute;left:110px;top:985px;width:440px;height:440px;border-radius:50%;border:22px solid var(--navy)}
.about-photo{position:absolute;left:136px;top:1011px;width:388px;height:388px;border-radius:50%;background:linear-gradient(135deg,#e5d6c6,#b48b6e 55%,#5b6874)}
.about-text{position:absolute;left:651px;top:1028px;width:420px}
.section-title{font-size:34px;font-weight:500;color:var(--dark)}
.rule{width:36px;height:3px;background:var(--navy);margin:18px 0 24px}
.about-text p{font-size:13.5px;line-height:26px}
/* services */
.services-bg{position:absolute;left:0;top:1440px;width:1200px;height:880px;background:linear-gradient(180deg,#eef1f4,#e3e7eb)}
.center-title{position:absolute;left:0;width:1200px;text-align:center}
.center-title .rule{margin:18px auto 0}
.service{position:absolute;width:314px;height:314px;border-radius:50%;text-align:center;color:var(--white);padding-top:130px}
.service h3{font-size:16px;font-weight:700}
.service .bar{width:30px;height:2px;background:var(--white);margin:14px auto}
.service p{font-size:13.5px;line-height:20px;padding:0 55px}
.service .go{width:12px;height:12px;border-radius:50%;background:var(--white);margin:10px auto 0}
.service .ico{position:absolute;left:50%;top:48px;margin-left:-28px;width:56px;height:60px}
.svc-navy{background:var(--navy)}
.svc-gray{background:var(--gray)}
/* team */
.team-card{position:absolute;top:2427px;width:232px;height:312px;background:var(--white);box-shadow:0 0 8px rgba(0,0,0,.15);padding:8px;text-align:center}
.team-photo{height:214px;background:linear-gradient(180deg,#e9ecef,#c9d0d6)}
.team-card h4{font-size:16px;font-weight:700;color:var(--dark);margin-top:16px}
.team-card span{font-size:12.5px;display:block;margin-top:6px}
/* as seen on */
.press{position:absolute;left:0;top:2838px;width:1200px;height:363px;background:var(--navy)}
.press-logo{position:absolute;top:174px;width:231px;height:106px;background:var(--white);border-radius:6px;display:flex;align-items:center;justify-content:center;gap:10px;font-size:19px;font-weight:700;color:var(--dark)}
.press-logo i{width:22px;height:22px;border-radius:50%;background:var(--gray);display:block}
.round-arrow{position:absolute;width:42px;height:42px;border-radius:50%;background:var(--white);display:flex;align-items:center;justify-content:center}
/* testimonial */
.quote-frame{position:absolute;left:129px;top:3361px;width:347px;height:263px;background:var(--navy)}
.quote-photo{position:absolute;left:137px;top:3370px;width:339px;height:254px;background:linear-gradient(135deg,#dfe4e8,#9aa7b3 60%,#3d5e8a)}
.quote-name{position:absolute;left:129px;top:3664px;width:268px;text-align:center;font-size:16px;color:var(--dark)}
.quote-name b{display:block;font-weight:700}
.quote-box{position:absolute;left:394px;top:3421px;width:627px;height:320px;background:var(--gray);padding:80px 32px 0 116px;color:var(--white)}
.quote-box p{font-size:13.5px;line-height:23px;font-style:italic;text-align:justify}
.stars{color:var(--orange);font-size:13px;margin-top:12px;letter-spacing:2px}
.qnav{position:absolute;top:3754px;width:34px;height:28px;background:var(--white);box-shadow:0 0 4px rgba(0,0,0,.25);display:flex;align-items:center;justify-content:center}
/* footer */
.footer-content{position:absolute;left:0;top:4100px;width:1200px;height:266px;color:#d8d8d8}
.footer-brand{position:absolute;left:110px;top:22px;display:flex;align-items:center;gap:12px}
.footer-brand .brand-dot{background:var(--white);width:60px;height:60px}
.footer-brand .brand-name{color:var(--white);font-size:32px;font-weight:500}
.footer-brand .brand-name small{color:var(--white);font-size:19px}
.footer-about{position:absolute;left:112px;top:118px;width:300px;font-size:13px;line-height:24px}
.socials{position:absolute;left:112px;top:184px;display:flex;gap:12px}
.socials i{width:30px;height:30px;border:1.5px solid #d8d8d8;border-radius:50%;display:block}
.fcol h5{font-size:13px;font-weight:700;text-decoration:underline;color:var(--white);margin-bottom:16px}
.fcol{position:absolute;top:22px;font-size:13px}
.fcol li{list-style:none;line-height:34px}
.fcol li::before{content:"»";margin-right:14px}
.contact-row{display:flex;align-items:center;gap:20px;margin-bottom:20px;line-height:20px}
.contact-row i{width:36px;height:36px;border:1.5px solid #d8d8d8;border-radius:50%;display:flex;align-items:center;justify-content:center;flex-shrink:0}
.bottom-bar{position:absolute;left:0;top:4366px;width:1200px;height:65px;background:var(--navy);color:var(--white);font-size:14px;text-align:center;line-height:65px}
</style>
</head>
<body>

<header class="site-header">
  <div class="brand"><span class="brand-dot"></span><div class="brand-name">MERIDALE<small>STAFFING</small></div></div>
  <div class="call">
    <span class="call-icon"><svg width="16" height="16" viewBox="0 0 24 24"><path fill="#fff" d="M6.6 10.8a15 15 0 0 0 6.6 6.6l2.2-2.2a1 1 0 0 1 1-.2 11.4 11.4 0 0 0 3.6.6 1 1 0 0 1 1 1V20a1 1 0 0 1-1 1A17 17 0 0 1 3 4a1 1 0 0 1 1-1h3.5a1 1 0 0 1 1 1c0 1.2.2 2.4.6 3.6a1 1 0 0 1-.3 1z"/></svg></span>
    <div class="call-text">CALL US TODAY !<b>+1 555 010 0199</b></div>
  </div>
  <nav class="main-nav"><span class="active">HOME</span><span>ABOUT</span><span>OUR SERVICES</span><span>REVIEWS</span><span>TEAM</span><span>BLOG</span><span>CONTACT US</span></nav>
</header>

<section class="hero">
  <div class="hero-photo" role="img" aria-label="Two colleagues in business attire reviewing work at a laptop in a bright office"></div>
  <svg class="abs" style="left:0;top:500px" width="1200" height="440" viewBox="0 0 1200 440">
    <path d="M0 180 C60 330 250 420 480 400 C760 375 980 250 1200 150 L1200 440 L0 440Z" fill="#fff"/>
    <path d="M0 180 C60 300 230 380 480 370 C780 355 1000 220 1200 160 L1200 180 C1000 250 780 390 480 405 C230 420 40 340 0 230Z" fill="#6d6e71"/>
  </svg>
  <h1>WE DO STAFF<br>AUGMENTATION<br>&amp; OPERATION<br>SUPPORT</h1>
  <div class="btn btn-navy" style="left:110px;top:479px;width:178px">Get Started<i></i></div>
  <div class="btn btn-orange" style="left:306px;top:479px;width:232px">Internal Recruiting<i></i></div>
  <svg class="slide-arrow" style="left:38px;top:300px" viewBox="0 0 30 40"><path d="M22 4 8 20l14 16" stroke="#0f3d66" stroke-width="3" fill="none"/></svg>
  <svg class="slide-arrow" style="left:1132px;top:300px" viewBox="0 0 30 40"><path d="M8 4l14 16L8 36" stroke="#0f3d66" stroke-width="3" fill="none"/></svg>
</section>

<section class="about">
  <div class="about-photo-ring"></div>
  <div class="about-photo" role="img" aria-label="Smiling business partners shaking hands over a laptop"></div>
  <div class="about-text">
    <h2 class="section-title">About Meridale Staffing</h2>
    <div class="rule"></div>
    <p>Lorem ipsum dolor sit amet, consectetur adipiscing elit, sed do eiusmod tempor incididunt ut labore et dolore magna aliqua. Ut enim ad minim veniam, quis nostrud exercitation ullamco laboris nisi ut aliquip ex ea commodo consequat. Duis aute irure dolor in reprehenderit in voluptate velit esse cillum dolore eu fugiat nulla pariatur. Excepteur sint occaecat cupidatat non proident, sunt in culpa qui officia deserunt mollit anim id est laborum Lorem ipsum dolor sit amet, consectetur adipiscing</p>
  </div>
  <div class="btn btn-navy" style="left:651px;top:1339px;width:178px">Learn More<i></i></div>
</section>

<section class="services">
  <div class="services-bg" role="img" aria-label="Faint backdrop of a business crowd and city skyline"></div>
  <svg class="abs" style="left:0;top:1430px" width="1200" height="900" viewBox="0 0 1200 900">
    <path d="M0 0 H1200 V30 C1000 -10 700 30 140 200 L0 240Z" fill="#fff"/>
    <path d="M140 200 C600 30 1000 -40 1200 120 L1200 20 C1000 -20 600 40 140 200Z" fill="#6d6e71"/>
    <path d="M0 640 C60 800 250 880 520 860 C820 835 1040 720 1200 640 L1200 900 L0 900Z" fill="#fff"/>
    <path d="M0 640 C50 770 240 840 520 830 C820 818 1040 710 1200 640 C1050 740 820 860 520 872 C240 882 40 800 0 700Z" fill="#6d6e71"/>
  </svg>
  <div class="center-title" style="top:1638px"><h2 class="section-title">Our Services</h2><div class="rule"></div></div>
  <div class="service svc-navy" style="left:147px;top:1754px">
    <svg class="ico" viewBox="0 0 56 60"><rect x="8" y="6" width="40" height="52" rx="3" fill="#fff"/><rect x="20" y="2" width="16" height="8" rx="2" fill="#fff"/><path d="M15 22h4M15 32h4M15 42h4M24 22h16M24 32h16M24 42h16" stroke="#0f3d66" stroke-width="3"/></svg>
    <h3>Background Verification</h3><div class="bar"></div><p>Sed ut perspiciatis unde mnis iste natus errovolutatem accusantium dolore</p><div class="go"></div>
  </div>
  <div class="service svc-gray" style="left:443px;top:1754px">
    <svg class="ico" viewBox="0 0 56 60"><circle cx="28" cy="16" r="10" fill="none" stroke="#fff" stroke-width="3"/><path d="M6 46c8-10 16-12 22-6 6-6 14-4 22 6" stroke="#fff" stroke-width="4" fill="none"/></svg>
    <h3>Performance Management</h3><div class="bar"></div><p>Sed ut perspiciatis unde mnis iste natus errovolutatem accusantium dolore</p><div class="go"></div>
  </div>
  <div class="service svc-navy" style="left:737px;top:1754px">
    <svg class="ico" viewBox="0 0 56 60"><circle cx="24" cy="26" r="16" fill="none" stroke="#fff" stroke-width="3"/><path d="M18 28l5 5 9-11M44 8v36M50 14v30" stroke="#fff" stroke-width="3" fill="none"/></svg>
    <h3>Behavioural Development</h3><div class="bar"></div><p>Sed ut perspiciatis unde mnis iste natus errovolutatem accusantium dolore</p><div class="go"></div>
  </div>
  <svg class="slide-arrow" style="left:38px;top:1891px" viewBox="0 0 30 40"><path d="M22 4 8 20l14 16" stroke="#0f3d66" stroke-width="3" fill="none"/></svg>
  <svg class="slide-arrow" style="left:1132px;top:1891px" viewBox="0 0 30 40"><path d="M8 4l14 16L8 36" stroke="#0f3d66" stroke-width="3" fill="none"/></svg>
</section>

<section class="team">
  <div class="abs" style="left:0;top:2560px;width:1200px;height:278px;background:linear-gradient(180deg,#fff,#e8ebee)"></div>
  <div class="center-title" style="top:2331px"><h2 class="section-title">Meet Our Team</h2><div class="rule"></div></div>
  <div class="team-card" style="left:107px"><div class="team-photo" role="img" aria-label="Portrait of a team member in a suit"></div><h4>Sam Rivera</h4><span>Founder &amp; Businessman</span></div>
  <div class="team-card" style="left:359px"><div class="team-photo" role="img" aria-label="Portrait of a team member in a blue suit"></div><h4>Sam Rivera</h4><span>Founder &amp; Businessman</span></div>
  <div class="team-card" style="left:612px"><div class="team-photo" role="img" aria-label="Portrait of a team member in a grey suit"></div><h4>Sam Rivera</h4><span>Founder &amp; Businessman</span></div>
  <div class="team-card" style="left:863px"><div class="team-photo" role="img" aria-label="Portrait of a team member in a dark suit"></div><h4>Sam Rivera</h4><span>Founder &amp; Businessman</span></div>
</section>

<section class="press">
  <div class="center-title" style="top:74px"><h2 class="section-title" style="color:#fff">As Seen On</h2><div class="rule" style="background:#fff"></div></div>
  <div class="round-arrow" style="left:31px;top:206px"><svg width="14" height="14" viewBox="0 0 14 14"><path d="M9 2 4 7l5 5" stroke="#2b2b2d" stroke-width="2" fill="none"/></svg></div>
  <div class="press-logo" style="left:113px"><i></i>Northbeam</div>
  <div class="press-logo" style="left:361px"><i></i>Relaymark</div>
  <div class="press-logo" style="left:609px"><i></i>Keystack</div>
  <div class="press-logo" style="left:856px"><i></i>Pivotline</div>
  <div class="round-arrow" style="left:1128px;top:206px"><svg width="14" height="14" viewBox="0 0 14 14"><path d="M5 2l5 5-5 5" stroke="#2b2b2d" stroke-width="2" fill="none"/></svg></div>
</section>

<section class="testimonials">
  <div class="center-title" style="top:3255px"><h2 class="section-title">What Our Clients Say</h2><div class="rule"></div></div>
  <div class="quote-box">
    <svg class="abs" style="left:116px;top:30px" width="58" height="42" viewBox="0 0 58 42"><path d="M0 42V22C0 8 8 1 22 0v8c-7 1-10 5-10 12h10v22zM34 42V22C34 8 42 1 56 0v8c-7 1-10 5-10 12h10v22z" fill="#fff"/></svg>
    <p>At vero eos et accusamus et iusto odio dignissimos ducimus qui blanditiis praesentium voluptatum deleniti atque corrupti quos dolores et quas molestias excepturi sint occaecati cupiditate non provident, similique sunt in culpa qui officia deserunt mollitia animi, id est laborum et dolorum fuga. Et harum quidem rerum facilis est et expedita distinctio. Nam libero tempore, cum soluta nobis est eligendi optio cumque</p>
    <div class="stars">★★★★★</div>
  </div>
  <div class="quote-frame"></div>
  <div class="quote-photo" role="img" aria-label="Smiling client in glasses and a blue suit"></div>
  <div class="quote-name"><b>SAM RIVERA</b>Businessman</div>
  <div class="qnav" style="left:932px"><svg width="14" height="12" viewBox="0 0 14 12"><path d="M13 6H2M6 1 1 6l5 5" stroke="#2b2b2d" stroke-width="2" fill="none"/></svg></div>
  <div class="qnav" style="left:983px"><svg width="14" height="12" viewBox="0 0 14 12"><path d="M1 6h11M8 1l5 5-5 5" stroke="#2b2b2d" stroke-width="2" fill="none"/></svg></div>
</section>

<footer>
  <svg class="abs" style="left:0;top:3840px" width="1200" height="530" viewBox="0 0 1200 530">
    <path d="M0 250 C300 120 700 50 1200 20 L1200 530 L0 530Z" fill="#6d6e71"/>
    <path d="M0 265 C320 150 700 90 1200 90 L1200 530 L0 530Z" fill="#2b2b2d"/>
  </svg>
  <div class="footer-content">
    <div class="footer-brand"><span class="brand-dot"></span><div class="brand-name">MERIDALE<small>STAFFING</small></div></div>
    <p class="footer-about">Ut enim ad minima veniam, quis nostrum exercitationem ullam corporis</p>
    <div class="socials"><i></i><i></i><i></i><i></i></div>
    <div class="fcol" style="left:460px">
      <h5>CONTACT US</h5>
      <div class="contact-row"><i><svg width="14" height="16" viewBox="0 0 14 18"><path d="M7 1a6 6 0 0 0-6 6c0 4 6 10 6 10s6-6 6-10a6 6 0 0 0-6-6z" stroke="#d8d8d8" stroke-width="1.5" fill="none"/><circle cx="7" cy="7" r="2" fill="#d8d8d8"/></svg></i><span>47 Alder Lane<br>Brookfield, MB - R0A 2B3</span></div>
      <div class="contact-row"><i><svg width="16" height="12" viewBox="0 0 16 12"><rect x="1" y="1" width="14" height="10" stroke="#d8d8d8" stroke-width="1.5" fill="none"/><path d="M1 1l7 6 7-6" stroke="#d8d8d8" stroke-width="1.5" fill="none"/></svg></i><span>info@meridalestaffing.example</span></div>
      <div class="contact-row"><i><svg width="14" height="14" viewBox="0 0 24 24"><path fill="#d8d8d8" d="M6.6 10.8a15 15 0 0 0 6.6 6.6l2.2-2.2a1 1 0 0 1 1-.2 11.4 11.4 0 0 0 3.6.6 1 1 0 0 1 1 1V20a1 1 0 0 1-1 1A17 17 0 0 1 3 4a1 1 0 0 1 1-1h3.5a1 1 0 0 1 1 1c0 1.2.2 2.4.6 3.6a1 1 0 0 1-.3 1z"/></svg></i><span style="font-weight:700;color:#fff;font-size:15px">+1 555 010 0199</span></div>
    </div>
    <div class="fcol" style="left:779px"><h5>QUICK LINKS</h5><ul><li>Home</li><li>About Us</li><li>Our Services</li><li>Blog</li><li>Reviews</li></ul></div>
    <div class="fcol" style="left:951px"><h5>OTHER LINKS</h5><ul><li>Contact Us</li><li>FAQ</li><li>Help Service</li><li>Terms Of Use</li><li>Privacy Policy</li></ul></div>
  </div>
  <div class="bottom-bar">© 2022 Meridale Staffing. All Rights Reserved</div>
</footer>

</body>
</html>
```